Book Cover - Life Lessons Book

I have written a book for my sons who are graduating high school and college. Working title is "Keep The Lantern Lit.....52 Porch Stories for Kin" I am looking for the book to appeal to young adults and parents who would want to give this book to them. It is a 125 page book that will be hardback and paperback - probably 5x8 or 6x9.
Updates

Reason: Altered some of the design elements based on the first submissions received. Would really like to have designs by Monday, May 15, 2016 but could not force a 2 day extension.

Target Market(s)

Young adults -- graduates, 20-3- year olds. And, parents would would give a book to their kids

Industry/Entity Type

Book Publisher

Font styles to use
Serif

Requirements
Must have
• Great design. It is a book cover so needs to catch the attention.
Nice to have
• I am open to more animated/playful/modern look or a more traditional look. Just would like to appeal to young adults and parents.
Should not have
• Anything in poor taste

```html
<!DOCTYPE html>
<html lang="en">
<head>
<meta charset="utf-8">
<title>Keep The Lantern Lit – Front Cover</title>
<link href="https://fonts.googleapis.com/css2?family=Open+Sans:wght@700;800&family=Playfair+Display:wght@900&family=Tinos&display=swap" rel="stylesheet">
<style>
  :root {
    --page-bg: #ffffff;
    --heading-grey: #8f8c86;
    --cover-teal: #4a6670;
    --cover-mid: #2e434b;
    --cover-edge: #0b1012;
    --title-white: #ffffff;
    --title-lime: #dcff00;
    --band-shade: rgba(20, 24, 22, 0.45);
    --subtitle-grey: #a9a6a1;
    --footer-bg: #182023;
    --footer-rule: #3f5560;
  }
  * { margin: 0; padding: 0; box-sizing: border-box; }
  html, body {
    width: 1200px; height: 1000px; overflow: hidden;
    background: var(--page-bg);
  }
  .canvas { position: relative; width: 1200px; height: 1000px; }

  .sheet-label {
    position: absolute; top: 10px; left: 0; width: 100%;
    text-align: center;
    font-family: "Tinos", "Times New Roman", serif;
    font-size: 33px; color: var(--heading-grey);
    letter-spacing: 0.5px;
  }

  .cover {
    position: absolute; left: 311px; top: 69px;
    width: 568px; height: 909px; overflow: hidden;
    background:
      radial-gradient(ellipse 75% 60% at 50% 45%, var(--cover-teal) 0%, var(--cover-mid) 60%, var(--cover-edge) 100%);
  }

  .title {
    position: absolute; left: 0; width: 100%;
    text-align: center;
    font-family: "Open Sans", Arial, sans-serif; font-weight: 800;
    line-height: 1; letter-spacing: -2px;
  }
  .title-keep { top: 68px; font-size: 104px; color: var(--title-white); }
  .title-the { top: 168px; font-size: 45px; color: var(--title-white); font-weight: 700; letter-spacing: -1px; }
  .title-lantern { top: 224px; font-size: 82px; color: var(--title-lime); }

  .subtitle-band {
    position: absolute; left: 0; top: 388px; width: 100%; height: 146px;
    background: var(--band-shade);
  }
  .subtitle-number {
    position: absolute; left: 104px; top: 2px;
    font-family: "Playfair Display", Georgia, serif; font-weight: 900;
    font-size: 150px; line-height: 1; color: var(--subtitle-grey);
  }
  .subtitle-words {
    position: absolute; left: 266px; top: 20px;
    font-family: "Open Sans", Arial, sans-serif; font-weight: 700;
    color: var(--subtitle-grey); text-align: center; line-height: 1;
  }
  .subtitle-top { font-size: 25px; letter-spacing: -0.5px; }
  .subtitle-for { font-size: 15px; margin-top: 9px; }
  .subtitle-main { font-size: 74px; letter-spacing: -2px; margin-top: -2px; }

  .author-bar {
    position: absolute; left: 0; top: 793px; width: 100%; height: 116px;
    background: var(--footer-bg);
    border-top: 3px solid var(--footer-rule);
    border-left: 3px solid var(--footer-rule);
    text-align: center; color: var(--title-white);
    font-family: "Tinos", "Times New Roman", serif;
  }
  .author-name { margin-top: 20px; font-size: 52px; line-height: 1; }
  .author-tagline { margin-top: 22px; font-size: 11px; letter-spacing: 5px; }
</style>
</head>
<body>
<div class="canvas">
  <div class="sheet-label">BOOK COVER (FRONT)</div>

  <div class="cover" role="img" aria-label="Book cover with a worn blue-grey textured background">
    <div class="title title-keep">KEEP</div>
    <div class="title title-the">THE</div>
    <div class="title title-lantern">LANTERN LIT</div>

    <div class="subtitle-band">
      <div class="subtitle-number">52</div>
      <div class="subtitle-words">
        <div class="subtitle-top">PORCH STORIES</div>
        <div class="subtitle-for">FOR</div>
        <div class="subtitle-main">KIN</div>
      </div>
    </div>

    <div class="author-bar">
      <div class="author-name">AUTHOR NAME</div>
      <div class="author-tagline">AUTHOR TAG LINE</div>
    </div>
  </div>
</div>
</body>
</html>
```